Business Cards

Need business card design that I can update for new employees and details. Needs to incorporate our logo, be bright and fun (in line with tourism and holidays)
Would like a Map of Western Australia on the front with locations all the caravan parks we own (just purchased Tom Price so please include that as well as others listed on our website).
Target Market(s)
Famillies
Contact Information for Business Card
5 Cards -
Neil Perrow (Director) e: perrow@wattlebay.com.au p: 0491 570 156
Mira Perrow (Director) e: perrow@wattlebay.com.au p: 0491 570 157
Owen Halvey (General Manager) e: halvey@wattlebay.com.au p: 0491 570 158
Helen Halvey (General Manager) e: halvey@wattlebay.com.au p: 0491 570 159
Colin Danby (Training and Operations Manager) - e: danby@wattlebay.com.au p:0491 570 110
Colors
Look and feel

```html
<!DOCTYPE html>
<html lang="en">
<head>
<meta charset="utf-8">
<title>Wattlebay Tourist Parks – Business Cards</title>
<link href="https://fonts.googleapis.com/css2?family=Cormorant+SC:wght@500&family=Roboto:wght@400&family=Roboto+Condensed:wght@500&display=swap" rel="stylesheet">
<style>
  :root {
    --teal: #00bccb;
    --teal-deep: #10b1c4;
    --sea-green: #56b9a3;
    --paper: #f7f8f8;
    --ink: #3a3a3a;
    --ground: #ecebe7;
    --faint-line: #dcf0f1;
    --faint-fill: #eaf5f5;
  }
  * { margin: 0; padding: 0; box-sizing: border-box; }
  html, body { width: 1200px; height: 800px; overflow: hidden; }
  body {
    background: var(--ground);
    font-family: "Roboto", Arial, sans-serif;
    position: relative;
  }
  .card {
    position: absolute;
    top: 245px;
    width: 540px;
    height: 310px;
    overflow: hidden;
    box-shadow: 0 6px 18px rgba(0,0,0,0.12);
  }
  .wordmark {
    font-family: "Cormorant SC", Georgia, serif;
    font-weight: 500;
    line-height: 1;
  }
  .wordmark-main { display: block; }
  .wordmark-main .initial { font-size: 1.45em; }
  .wordmark-sub { display: block; }

  /* Personal side */
  .card-personal { left: 40px; background: var(--paper); }
  .watermark-square {
    position: absolute;
    right: 22px; top: 18px;
    width: 236px; height: 236px;
    border: 8px solid var(--faint-line);
    background: var(--faint-fill);
  }
  .side-band {
    position: absolute;
    left: 40px; top: 0;
    width: 72px; height: 100%;
    background: var(--teal);
  }
  .band-mark {
    position: absolute;
    left: 12px; top: 68px;
    width: 48px; height: 48px;
    border: 3px solid #fff;
    background: var(--sea-green);
  }
  .band-icons {
    position: absolute;
    left: 0; top: 182px;
    width: 72px;
    display: flex; flex-direction: column; align-items: center; gap: 14px;
  }
  .band-icons svg { width: 14px; height: 14px; fill: #fff; }
  .wordmark-small {
    position: absolute;
    left: 138px; top: 58px;
    color: var(--ink);
  }
  .wordmark-small .wordmark-main { font-size: 24px; letter-spacing: 3px; }
  .wordmark-small .wordmark-sub { font-size: 12px; letter-spacing: 3px; margin: 2px 0 0 42px; }
  .person {
    position: absolute;
    left: 138px; top: 148px;
  }
  .person-name {
    font-family: "Roboto Condensed", "Arial Narrow", sans-serif;
    font-weight: 500;
    font-size: 24px;
    color: var(--teal-deep);
    text-transform: uppercase;
  }
  .person-role {
    font-family: "Roboto Condensed", "Arial Narrow", sans-serif;
    font-weight: 500;
    font-size: 16px;
    color: var(--teal-deep);
    text-transform: uppercase;
    margin-top: 2px;
  }
  .contact-list {
    list-style: none;
    margin-top: 12px;
    font-size: 14px;
    line-height: 20px;
    color: var(--ink);
  }

  /* Brand side */
  .card-brand { left: 620px; background: var(--teal); color: #fff; }
  .brand-square {
    position: absolute;
    left: 250px; top: 52px;
    width: 82px; height: 82px;
    border: 4px solid #fff;
    background: var(--sea-green);
  }
  .wordmark-large {
    position: absolute;
    left: 0; right: 0; top: 138px;
    text-align: center;
  }
  .wordmark-large .wordmark-main { font-size: 34px; letter-spacing: 6px; }
  .wordmark-large .wordmark-sub { font-size: 16px; letter-spacing: 4px; margin-top: 4px; }
  .brand-url {
    position: absolute;
    left: 0; right: 0; top: 238px;
    text-align: center;
    font-size: 14px;
    letter-spacing: 3px;
  }
</style>
</head>
<body>

  <section class="card card-personal">
    <div class="watermark-square"></div>
    <div class="side-band">
      <div class="band-mark"></div>
      <div class="band-icons">
        <svg viewBox="0 0 16 16" aria-label="person"><circle cx="8" cy="5" r="3.5"/><path d="M1 16c0-4 3-6 7-6s7 2 7 6z"/></svg>
        <svg viewBox="0 0 16 16" aria-label="phone"><path d="M3 1l3 3-2 2c1 2 3 4 5 5l2-2 3 3-2 3C7 15 1 9 1 3z"/></svg>
        <svg viewBox="0 0 16 16" aria-label="email"><path d="M1 3h14v10H1z M2 4l6 5 6-5" fill="#fff" stroke="#00bccb" stroke-width="1"/></svg>
        <svg viewBox="0 0 16 16" aria-label="website"><circle cx="8" cy="8" r="7"/><path d="M1 8h14M8 1c-3 4-3 10 0 14M8 1c3 4 3 10 0 14" stroke="#00bccb" stroke-width="1" fill="none"/></svg>
      </div>
    </div>
    <div class="wordmark wordmark-small">
      <span class="wordmark-main"><span class="initial">W</span>attlebay</span>
      <span class="wordmark-sub">Tourist Parks</span>
    </div>
    <div class="person">
      <div class="person-name">Neil Perrow</div>
      <div class="person-role">Director</div>
      <ul class="contact-list">
        <li>0491 570 156</li>
        <li>perrow@wattlebay.com.au</li>
        <li>www.wattlebay.com.au</li>
      </ul>
    </div>
  </section>

  <section class="card card-brand">
    <div class="brand-square"></div>
    <div class="wordmark wordmark-large">
      <span class="wordmark-main"><span class="initial">W</span>attlebay</span>
      <span class="wordmark-sub">Tourist Parks</span>
    </div>
    <div class="brand-url">www.wattlebay.com.au</div>
  </section>

</body>
</html>
```